Buch-/E-Book-Cover im Bereich der Persönlichkeitsentwicklung
Vielen lieben Dank für die super Arbeit von Dir. Das Design ist klasse und die vielen Vorschläge waren auch super. Die komplette Zusammenarbeit verlief sehr professionell und Änderungswünsche wurden sehr schnell umgesetzt. Ich kann Dich voll und ganz weiterempfehlen.
Zielgruppe
Wir arbeiten in der Persönlichkeitsentwicklung für Jugendliche. Dabei spezialisieren wir uns auf den Altersbereich 12 - 17 Jahre. Unser Ziel ist es jungen Menschen zu zeigen, wie Sie zu sich selbst finden und ein glückliches sowie erfolgreiches Leben führen können.
Aufgabenstellung
- Das Design sollte für die Eltern von Teenagern und auch für die Teenager selbst ausgelegt werden. Das Buch ist für die Jugendlichen (Mädchen und Jungen im Alter zwischen 12 Jahren und 17 Jahren) gedacht, wird allerdings meist von deren Mütter gekauft.
- Der Name des Autors lautet: Henrik Falbe
- Der Titel lautet: Junge Herzen finden Mut und Richtung
- Der Untertitel lautet: Was Heranwachsende über ihren Weg lernen
- Im Anhang befinden sich Designs, die ich gut finde (nur falls jemand weitere Ideen haben möchte)
- Format: 15,24 cm x 22,86 cm (6' x 9') [genaue Maße fürs Taschenbuch und Hardcover sind im Anhang (.zip Dateien)]
1. E-Book:
- Coverdateien sollten idealerweise 2 560 Pixel hoch und 1 600 Pixel breit sein. Zur Gewährleistung der bestmöglichen Qualität (insbesondere auf HD-Geräten) sollte das Bild mindestens 2 500 Pixel hoch sein.
- Format: TIFF (.tif/.tiff) oder JPEG (.jpeg/.jpg)
- DPI: 72 dpi
- Größe: Ihr Coverbild muss kleiner als 50 MB sein.
Hinweis: Vermeiden Sie es, Ihre Dateien zu komprimieren. Dies kann die Qualität Ihres Covers auf Lesegeräten beeinträchtigen. Das beste Ergebnis erzielen Sie mit Bildern, die eine Mindestauflösung von 300 ppi (Pixels per Inch) haben.
- Rahmen: Coverbilder mit weißem oder sehr hellem Hintergrund heben sich kaum vom weißen Hintergrund ab. Fügen Sie einen dünnen Rahmen (3–4 Pixel) in Mittelgrau hinzu, um die Ränder des Covers besser sichtbar zu machen.
2. + 3. Taschenbuch/Hardcover [genaue Maße fürs Taschenbuch und Hardcover sind im Anhang (.zip Dateien)] :
- Dateityp: Das Cover muss als einzelne PDF-Datei vorliegen und die hintere Coverseite, den Buchrücken und die vordere Coverseite als einzelnes Bild enthalten.
- Dateigröße: Coverdateien, die größer als 650 MB sind, können nicht konvertiert werden. Die Datei sollte maximal 40 MB groß sein, da sich bei großen Dateien der Druck verlangsamt.
- Die gen..

```html
<!DOCTYPE html>
<html lang="de">
<head>
<meta charset="utf-8">
<title>Junge Herzen finden Mut und Richtung – Umschlag</title>
<link rel="stylesheet" href="https://fonts.googleapis.com/css2?family=Barlow+Condensed:wght@400;500;700&family=Cabin+Sketch:wght@700&family=Amatic+SC:wght@700&display=swap">
<style>
  :root {
    --sky-top: #b9d6f0;
    --sky-mid: #cfe3f4;
    --sky-low: #f6f8fa;
    --ink: #1c1c1c;
    --taupe: #6f6a5c;
    --orange: #e46e1c;
    --trim: #9ea4aa;
    --rock-dark: #4e4b46;
    --rock-light: #8d887f;
  }
  html, body {
    margin: 0;
    width: 1200px;
    height: 880px;
    overflow: hidden;
    background: #ffffff;
  }
  .spread {
    position: absolute;
    left: 36px; top: 44px;
    width: 1130px; height: 792px;
    border: 1px solid var(--trim);
    box-sizing: border-box;
    overflow: hidden;
  }
  .panel { position: absolute; top: 0; height: 100%; }
  .back {
    left: 0; width: 529px;
    background: linear-gradient(180deg, var(--sky-top) 0%, var(--sky-mid) 45%, var(--sky-low) 100%);
  }
  .spine {
    left: 529px; width: 72px;
    background: linear-gradient(180deg, var(--sky-top) 0%, var(--sky-mid) 55%, var(--sky-low) 100%);
    border-left: 1px solid rgba(255,255,255,.7);
    border-right: 1px solid rgba(255,255,255,.7);
    box-sizing: border-box;
  }
  .front {
    left: 601px; width: 529px;
    background: linear-gradient(180deg, var(--sky-top) 0%, #c7def3 60%, #d7e7f5 100%);
  }

  /* back cover */
  .blurb {
    position: absolute; left: 44px; top: 50px; width: 370px;
    font-family: "Barlow Condensed", sans-serif;
    color: var(--ink);
    font-size: 13.4px; line-height: 17.6px;
  }
  .blurb h2 {
    margin: 0 0 9px;
    font-size: 15.5px; font-weight: 700;
    color: var(--taupe);
  }
  .blurb p { margin: 0 0 17px; }
  .blurb h3 { margin: 0 0 4px; font-size: 13.6px; font-weight: 700; }
  .blurb ul { margin: 0; padding: 0; list-style: none; }
  .blurb li::before { content: "· "; font-weight: 700; }

  .testimonial {
    position: absolute; left: 183px; top: 554px; width: 320px;
    font-family: "Amatic SC", cursive;
    font-weight: 700;
    font-size: 23px; line-height: 25.5px;
    color: var(--taupe);
    margin: 0;
  }
  .testimonial cite { display: block; margin-top: 6px; font-style: normal; }

  /* spine */
  .spine-text {
    position: absolute; left: 50%;
    writing-mode: vertical-rl;
    transform: translateX(-50%) rotate(180deg);
    white-space: nowrap;
  }
  .spine-title { top: 54px; font-family: "Cabin Sketch", sans-serif; font-size: 28px; color: var(--taupe); }
  .spine-title .small { font-family: "Barlow Condensed", sans-serif; font-size: 22px; font-weight: 400; }
  .spine-title .accent { color: var(--orange); }
  .spine-author {
    top: 604px;
    font-family: "Barlow Condensed", sans-serif; font-weight: 700;
    font-size: 21px; letter-spacing: 1px; color: var(--ink);
  }

  /* front cover */
  .author {
    position: absolute; top: 26px; left: 0; width: 100%;
    text-align: center;
    font-family: "Barlow Condensed", sans-serif; font-weight: 700;
    font-size: 23px; letter-spacing: 1.2px; color: var(--ink);
    margin: 0;
  }
  .title { margin: 0; font-weight: 400; }
  .title span { position: absolute; white-space: nowrap; line-height: 1; }
  .t-big { font-family: "Cabin Sketch", sans-serif; font-weight: 700; }
  .t-small { font-family: "Barlow Condensed", sans-serif; color: var(--taupe); }
  .t-line1 { left: 40px; top: 118px; font-size: 64px; color: var(--taupe); }
  .t-finden { left: 196px; top: 196px; font-size: 38px; }
  .t-mut { left: 50px; top: 238px; font-size: 128px; color: var(--orange); }
  .t-und { left: 280px; top: 302px; font-size: 38px; }
  .t-richtung { left: 186px; top: 370px; font-size: 72px; color: var(--orange); }

  .subtitle {
    position: absolute; left: 20px; top: 448px; width: 175px;
    margin: 0;
    text-align: right;
    font-family: "Amatic SC", cursive; font-weight: 700;
    font-size: 25px; line-height: 30px; color: var(--ink);
  }

  .cover-photo {
    position: absolute; left: 48px; bottom: 0;
    width: 481px; height: 255px;
    background:
      linear-gradient(180deg, rgba(185,214,240,0) 0%, rgba(185,214,240,0) 38%, var(--rock-light) 62%, var(--rock-dark) 100%);
  }
</style>
</head>
<body>
<div class="spread">

  <section class="panel back">
    <div class="blurb">
      <h2>Dein wahres Selbst verändert Dein Leben ins Positive.</h2>
      <p>Glaubst Du, dass Du zu mehr in der Lage bist? Geraten deine Träume wegen Verpflichtungen, Ängsten und dem Alltag in den Hintergrund? Würdest Du gerne ein Mittel haben, das gegen Leistungsdruck und Zeitmangel hilft? Denkst Du, dass Du mit der richtigen Lebensweise ein komplett anderes, viel erfüllteres Leben führen könntest? Dieses Buch zeigt dir den Weg dahin.</p>
      <p>Im Gegensatz zu zahlreichen anderen Ratgebern wird in diesem Buch das Thema Selbstfindung viel tiefgehender und individueller betrachtet. Häufig wird nur sehr oberflächlich nach dem idealen Beruf gesucht, darüber geschrieben, wie wir unseren Alltag verbringen sollten oder wie Du zu dir selbst findest. Deshalb erhältst Du hier einige lebensnahe Praxisbeispiele, die Du sofort anwenden kannst.</p>
      <h3>In diesem Buch lernst Du unter anderem, wie Du</h3>
      <ul>
        <li>den passenden Beruf findest.</li>
        <li>dich von Ängsten befreien kannst.</li>
        <li>Klarheit darüber erlangst, was Du in deinem Leben willst.</li>
        <li>innere und äußere Freiheit erlangst.</li>
        <li>mit dem richtigen Mindset, mehr Energie bekommst.</li>
        <li>in die Umsetzung kommst.</li>
        <li>mit Deinen Gefühlen umgehen kannst.</li>
      </ul>
    </div>
    <blockquote class="testimonial">„Das FUNKE-Prinzip hat mich sehr beeindruckt und nachhaltig beeinflusst. Es ist absolut lesenswert und im Vergleich zu anderen Ratgebern spricht es den Leser direkt an und motiviert zum Handeln und Nachdenken.“
      <cite>Lehrerin Fr. Wendler</cite>
    </blockquote>
  </section>

  <section class="panel spine">
    <div class="spine-text spine-title">Junge Herzen <span class="small">finden</span> <span class="accent">Mut</span> <span class="small">und</span> <span class="accent">Richtung</span></div>
    <div class="spine-text spine-author">HENRIK FALBE</div>
  </section>

  <section class="panel front">
    <p class="author">HENRIK FALBE</p>
    <h1 class="title">
      <span class="t-big t-line1">Junge Herzen</span>
      <span class="t-small t-finden">finden</span>
      <span class="t-big t-mut">Mut</span>
      <span class="t-small t-und">und</span>
      <span class="t-big t-richtung">Richtung</span>
    </h1>
    <p class="subtitle">WAS HERANWACHSENDE ÜBER IHREN WEG LERNEN</p>
    <div class="cover-photo" role="img" aria-label="Foto: vier Jugendliche sitzen vor blauem Himmel auf einer alten Steinmauer"></div>
  </section>

</div>
</body>
</html>
```